zAvora Corporate Website

zAvora is a well-funded start up developing an Online Marketing Platform for small businesses in Europe.
We are launching in February 2012 with all-in-one online marketing services including professional website, DIY SEO, Dashboard with Reports and Online marketing tools, and Support.
Our internal web designer has come up with a preliminary website design which we wish to continue to improve using new ideas, colours, layout, image, etc.
The brief is very simple - improve the website whether it is look & feel, ease of use, conversion rate - we are looking for overall improvements.
The contest will last 5 days and we will award the winner £300.
If you are the winner , you will also be required to provide designs for 3 more internal pages adhering to the proposed home page design.
Judging criteria : -
Visual Design
Layout must adhere to best practices and wire frame. If you decide to move elements around significantly please provide reason
Functional, informative and drives calls to action
Industry/Entity Type
Marketing
Look and feel
Each slider illustrates characteristics of the customer's brand and the style your logo design should communicate.

```html
<!DOCTYPE html>
<html lang="en">
<head>
<meta charset="utf-8">
<title>zAvora – Online Marketing for Small Business</title>
<link href="https://fonts.googleapis.com/css2?family=Ubuntu:ital,wght@0,400;0,500;0,700;1,500&family=Open+Sans:wght@400;600;700&display=swap" rel="stylesheet">
<style>
:root{
  --sky-top:#1596d6;
  --sky-bottom:#4bbbe9;
  --ink:#0f2f45;
  --brand-blue:#1d6fa3;
  --teal-deep:#0e5a7e;
  --teal-light:#4fc6f2;
  --page:#f2f3f5;
  --card:#ffffff;
  --text-grey:#6d6d6d;
  --line:#d6d9dd;
  --slider-frame:#3b86ab;
  --slider-fill:#a9d6ea;
  --promo-frame:#0c3f58;
  --promo-grey:#d9dadb;
  --promo-purple:#7d69a6;
  --promo-green:#8dc43e;
  --promo-red:#e5213a;
  --promo-bar:#3592c4;
  --info-blue:#b2e2f6;
  --footer:#2d2d2d;
  --footer-deep:#222222;
  --footer-text:#b9b9b9;
}
*{box-sizing:border-box;margin:0;padding:0}
html,body{width:843px;height:1200px;overflow:hidden}
body{position:relative;background:var(--page);font-family:"Open Sans",sans-serif;color:var(--text-grey)}
.abs{position:absolute}

.top-strip{left:0;top:0;width:843px;height:17px;background:#000}
.hero{left:0;top:17px;width:843px;height:329px;background:linear-gradient(180deg,var(--sky-top),var(--sky-bottom))}
.brand{left:55px;top:37px;display:flex;align-items:center;gap:6px;color:#fff;font-family:"Ubuntu",sans-serif;font-size:33px;font-weight:500}
.brand-dot{width:32px;height:32px;border-radius:50%;background:#fff}

.nav{left:0;top:48px;width:843px;height:28px;font-family:"Ubuntu",sans-serif;font-size:14px;color:#fff}
.nav a{position:absolute;top:0;color:#fff;text-decoration:none;line-height:28px;white-space:nowrap}
.nav a.current{left:320px;width:62px;text-align:center;background:#fff;color:#1a8fd0;border-radius:14px}
.nav .divider{position:absolute;top:-2px;width:1px;height:32px;background:rgba(255,255,255,.3)}

.features{left:46px;top:114px;width:180px;list-style:none;font-family:"Ubuntu",sans-serif;font-size:15px;color:#fff;background:linear-gradient(90deg,rgba(255,255,255,.18),rgba(255,255,255,0))}
.features li{display:flex;align-items:center;gap:6px;height:26.5px;padding-left:12px;border-bottom:1px solid rgba(255,255,255,.2);white-space:nowrap}
.features svg{flex:none}
.tagline{left:55px;top:235px;font-family:"Ubuntu",sans-serif;font-size:16px;line-height:20px;color:var(--ink)}
.free-btn{left:55px;top:282px;width:117px;height:37px;border-radius:4px;background:linear-gradient(#fafafa,#cfd2d5);border:1px solid #b9bcbf;text-align:center;color:#222;font-family:"Ubuntu",sans-serif;text-decoration:none}
.free-btn b{display:block;font-size:16px;line-height:18px;margin-top:4px}
.free-btn span{display:block;font-size:11px;line-height:11px}
.hero-person{left:282px;top:140px;width:285px;height:206px;background:linear-gradient(180deg,#c99a7b 0%,#b88664 45%,#eef1f4 60%,#dfe4e8 100%);border-radius:120px 120px 0 0}
.bubble{position:absolute;background:linear-gradient(#fff,#e6f2f8);border-radius:4px;padding:3px 7px;font-size:12px;color:#2b4c66;font-family:"Open Sans",sans-serif;box-shadow:0 1px 3px rgba(0,0,0,.2);white-space:nowrap}
.bubble::after{content:"";position:absolute;left:9px;bottom:-6px;border:6px solid transparent;border-top-color:#e6f2f8;border-bottom:0}

.headline-band{left:43px;top:346px;width:754px;height:60px;background:var(--teal-deep);border-radius:0 0 6px 6px;text-align:center;box-shadow:0 3px 5px rgba(0,0,0,.25)}
.headline-band h1{font-family:"Ubuntu",sans-serif;font-weight:500;font-size:20px;line-height:24px;color:#fff;margin-top:7px;white-space:nowrap}
.headline-band p{font-family:"Ubuntu",sans-serif;font-style:italic;font-weight:500;font-size:14px;line-height:18px;color:var(--teal-light);margin-top:3px}

.examples-title{left:22px;top:442px;font-family:"Ubuntu",sans-serif;font-weight:400;font-size:18px;color:var(--brand-blue);white-space:nowrap}
.examples-text{left:22px;top:468px;width:600px;font-size:9px;line-height:15px}
.slider{left:20px;top:522px;width:592px;height:123px;background:var(--slider-fill);border:4px solid var(--slider-frame)}
.slide{position:absolute;top:10px;width:132px;height:96px;border:3px solid #fff;box-shadow:0 0 2px rgba(0,0,0,.3)}
.slider-arrow{position:absolute;top:44px}

.news{left:624px;top:432px;width:195px;height:231px;background:var(--card);border:1px solid var(--line);border-radius:8px;padding:8px 17px}
.news h2{font-family:"Ubuntu",sans-serif;font-weight:400;font-size:18px;color:var(--brand-blue)}
.news time{display:block;font-size:10px;color:#333;margin-top:12px}
.news p{font-size:9px;line-height:13.5px;margin-top:8px}

.promo{left:18px;top:678px;width:611px;height:146px;background:var(--promo-frame)}
.offer{position:absolute;top:8px;width:190px;height:124px;overflow:hidden;font-family:"Ubuntu",sans-serif;color:#fff}
.offer .price{position:absolute;right:-20px;top:-22px;width:78px;height:78px;border-radius:50%;background:var(--promo-red);padding:24px 0 0 10px;font-size:19px;font-weight:700;line-height:18px;white-space:nowrap}
.offer .price small{display:block;font-size:8px;font-weight:500}
.offer .burst{position:absolute;left:10px;top:18px;width:62px;height:62px}
.offer .burst span{position:absolute;inset:0;display:flex;align-items:center;justify-content:center;text-align:center;font-size:10px;font-weight:700;line-height:11px;transform:rotate(-14deg)}
.offer .big{position:absolute;left:70px;top:48px;font-size:27px;font-weight:500;line-height:24px;white-space:nowrap}
.offer .big .lead{display:block;font-size:19px;line-height:20px}
.offer .bar{position:absolute;left:0;bottom:0;width:100%;height:23px;background:var(--promo-bar);font-size:11px;text-align:center;line-height:23px;white-space:nowrap}
.how{left:628px;top:678px;width:186px;height:146px;background:var(--info-blue);padding:14px 14px}
.how h2{font-family:"Ubuntu",sans-serif;font-weight:400;font-size:16px;color:#111}
.how p{font-size:9px;line-height:13px;color:#333;margin-top:5px}

.feature-card{top:845px;width:198px;height:101px;background:linear-gradient(#fff,#f5f6f8);border:1px solid var(--line);border-bottom:0;padding:10px 16px}
.feature-card h3{display:flex;align-items:center;gap:8px;height:26px;font-family:"Ubuntu",sans-serif;font-weight:400;font-size:16px;color:#222;white-space:nowrap}
.feature-card p{font-size:8.6px;line-height:14px;margin-top:8px}

.footer{left:0;top:968px;width:843px;height:184px;background:var(--footer);border-top:3px solid #8a8a8a}
.footer-col{position:absolute;top:18px}
.footer-col ul{list-style:none;margin-top:10px;font-size:10px;line-height:18px;color:var(--footer-text);white-space:nowrap}
.footer-col .rule{width:160px;height:1px;background:#444;margin-top:4px}
.newsletter p{font-size:10px;color:var(--footer-text);margin-top:8px;white-space:nowrap}
.newsletter input{margin-top:6px;width:148px;height:15px;border:0;font-size:8px;padding:0 4px;font-family:"Open Sans",sans-serif}
.bottom-bar{left:0;top:1152px;width:843px;height:48px;background:var(--footer-deep);text-align:right;padding:13px 45px 0 0;font-size:9.5px;color:var(--footer-text)}
</style>
</head>
<body>
<div class="abs top-strip"></div>

<header class="abs hero"></header>
<div class="abs brand"><span class="brand-dot"></span>zAvora</div>
<nav class="abs nav">
  <a class="current" href="#">Home</a>
  <span class="divider" style="left:392px"></span>
  <a href="#" style="left:416px">About Us</a>
  <span class="divider" style="left:491px"></span>
  <a href="#" style="left:518px">Quick Tour</a>
  <span class="divider" style="left:603px"></span>
  <a href="#" style="left:628px">Pricing</a>
  <span class="divider" style="left:690px"></span>
  <a href="#" style="left:713px">Contact Us</a>
</nav>

<ul class="abs features">
  <li><svg width="16" height="16" viewBox="0 0 16 16"><rect width="16" height="16" rx="3" fill="#fff"/><path d="M4 8l3 3 5-6" stroke="#1a8fd0" stroke-width="2.2" fill="none"/></svg>Business Websites</li>
  <li><svg width="16" height="16" viewBox="0 0 16 16"><rect width="16" height="16" rx="3" fill="#fff"/><path d="M4 8l3 3 5-6" stroke="#1a8fd0" stroke-width="2.2" fill="none"/></svg>Online Marketing</li>
  <li><svg width="16" height="16" viewBox="0 0 16 16"><rect width="16" height="16" rx="3" fill="#fff"/><path d="M4 8l3 3 5-6" stroke="#1a8fd0" stroke-width="2.2" fill="none"/></svg>Dashboard Controls</li>
  <li><svg width="16" height="16" viewBox="0 0 16 16"><rect width="16" height="16" rx="3" fill="#fff"/><path d="M4 8l3 3 5-6" stroke="#1a8fd0" stroke-width="2.2" fill="none"/></svg>Full Setup &amp; Support</li>
</ul>
<p class="abs tagline">Getting a Website has never<br>been so simple</p>
<a class="abs free-btn" href="#"><b>FREE !</b><span>sign up now for</span></a>

<div class="abs hero-person" role="img" aria-label="Photo of a thoughtful man scratching his head, surrounded by marketing questions"></div>
<div class="bubble" style="left:262px;top:152px">SEO?</div>
<div class="bubble" style="left:316px;top:149px">Reports?</div>
<div class="bubble" style="left:382px;top:145px">Refferals?</div>
<div class="bubble" style="left:474px;top:145px">Friendbook?</div>
<div class="bubble" style="left:555px;top:149px">Maintenence?</div>
<div class="bubble" style="left:647px;top:152px">Directories?</div>
<div class="bubble" style="left:730px;top:142px">Website?</div>
<div class="bubble" style="left:284px;top:180px">Banners?</div>
<div class="bubble" style="left:357px;top:176px">Content?</div>
<div class="bubble" style="left:499px;top:176px">Testimonials?</div>
<div class="bubble" style="left:589px;top:180px">Promotions?</div>
<div class="bubble" style="left:666px;top:184px">Chirper?</div>
<div class="bubble" style="left:720px;top:169px">Images?</div>
<div class="bubble" style="left:329px;top:208px">Support?</div>
<div class="bubble" style="left:515px;top:208px">Email Marketing?</div>
<div class="bubble" style="left:626px;top:211px">Searchly?</div>
<div class="bubble" style="left:289px;top:218px">PPC?</div>
<div class="bubble" style="left:543px;top:230px">Blogs?</div>

<section class="abs headline-band">
  <h1>The Complete Online Marketing Solution for Small Business Websites</h1>
  <p>“Get a big online presence and more sales leads in 30 minutes”</p>
</section>

<h2 class="abs examples-title">View Examples of Our Stunning Business Websites</h2>
<p class="abs examples-text">Brightwell eSolutions is specialized in handling advanced web projects and the ongoing projects that require permanent maintenance and support .We like challenges and do complete these challenge with expertise we like solving questions that arises in such projects as these helps us to grow also.</p>
<div class="abs slider">
  <svg class="slider-arrow" style="left:4px" width="10" height="26" viewBox="0 0 10 26"><path d="M8 1L2 13l6 12" stroke="#2a7fb0" stroke-width="2" fill="none"/></svg>
  <div class="slide" style="left:18px;background:linear-gradient(#e9eef2,#c9d6e0)" role="img" aria-label="Example business website for a consulting firm"></div>
  <div class="slide" style="left:156px;background:linear-gradient(#2b2b2b,#6b6b6b)" role="img" aria-label="Example business website for a music teacher"></div>
  <div class="slide" style="left:296px;background:linear-gradient(#f3f6f8,#cfe3ef)" role="img" aria-label="Example business website for a medical practice"></div>
  <div class="slide" style="left:437px;background:linear-gradient(#4a3f8f,#8f88b8)" role="img" aria-label="Example business website for an online shop"></div>
  <svg class="slider-arrow" style="left:570px" width="10" height="26" viewBox="0 0 10 26"><path d="M2 1l6 12-6 12" stroke="#2a7fb0" stroke-width="2" fill="none"/></svg>
</div>

<aside class="abs news">
  <h2>News &amp; Blog</h2>
  <time>20.11.2011</time>
  <p>Brightwell eSolutions is specialized in handling advanced web projects and the ongoing projects that require permanent maintenance</p>
  <time>20.11.2011</time>
  <p>Brightwell eSolutions is specialized in handling advanced web projects and the ongoing projects that require permanent maintenance</p>
</aside>

<section class="abs promo">
  <div class="offer" style="left:12px;background:var(--promo-grey)">
    <div class="price">£ 199<small>Value</small></div>
    <div class="big" style="left:42px;top:50px;font-size:36px;line-height:40px">Setup</div>
    <svg class="burst" viewBox="0 0 62 62"><polygon points="31,0 37,12 50,6 49,20 62,24 52,33 60,45 46,46 44,60 33,51 22,60 19,47 5,48 11,35 0,27 13,21 10,7 24,12" fill="var(--promo-bar)"/></svg>
    <div class="burst"><span style="font-size:19px">FREE</span></div>
    <div class="bar" style="font-size:16px;font-weight:500">Web offer only</div>
  </div>
  <div class="offer" style="left:213px;background:var(--promo-purple)">
    <div class="price">£ 22<small>per month</small></div>
    <svg class="burst" style="top:38px" viewBox="0 0 62 62"><polygon points="31,0 37,12 50,6 49,20 62,24 52,33 60,45 46,46 44,60 33,51 22,60 19,47 5,48 11,35 0,27 13,21 10,7 24,12" fill="var(--promo-bar)"/></svg>
    <div class="burst" style="top:38px"><span>PRO<br>PACKAGE</span></div>
    <div class="big"><span class="lead" style="color:var(--promo-green)">Big online</span>presence</div>
    <div class="bar">Business Website &amp; Easy Dashboard</div>
  </div>
  <div class="offer" style="left:411px;background:var(--promo-green)">
    <div class="price">£ 29<small>per month</small></div>
    <svg class="burst" style="top:38px" viewBox="0 0 62 62"><polygon points="31,0 37,12 50,6 49,20 62,24 52,33 60,45 46,46 44,60 33,51 22,60 19,47 5,48 11,35 0,27 13,21 10,7 24,12" fill="var(--promo-bar)"/></svg>
    <div class="burst" style="top:38px"><span>TURBO<br>SALES<br>PRO PLUS</span></div>
    <div class="big" style="left:66px;top:46px"><span class="lead" style="color:var(--promo-purple)">More sales</span><span style="margin-left:18px">leads</span></div>
    <div class="bar" style="height:28px;line-height:11px;padding-top:3px;font-size:10.5px">Business Website, Easy Dashboard<br>&amp;PPC Sales</div>
  </div>
</section>
<section class="abs how">
  <h2>How does it Work ?</h2>
  <p>Brightwell eSolutions provides you the Search Engine Optimization making your website search engine friendly. So that the website can achieve top position and ranking in the Internet searches and thereby increasing the scope for the website</p>
</section>

<article class="abs feature-card" style="left:19px">
  <h3><svg width="30" height="22" viewBox="0 0 30 22"><path d="M2 2v18h26" stroke="#222" stroke-width="2" fill="none"/><path d="M5 16l6-7 5 4 8-10" stroke="#222" stroke-width="2" fill="none"/></svg>Cast Studies</h3>
  <p>We like challenges and do complete these challenge with expertise we like solving questions that arises</p>
</article>
<article class="abs feature-card" style="left:221px">
  <h3><svg width="22" height="24" viewBox="0 0 22 24"><circle cx="11" cy="11" r="6" fill="#222"/><rect x="8" y="17" width="6" height="4" fill="#222"/><path d="M11 0v3M2 4l2 2M20 4l-2 2M0 11h3M19 11h3" stroke="#222" stroke-width="1.5"/></svg>How to Get</h3>
  <p>We like challenges and do complete these challenge with expertise we like solving questions that arises</p>
</article>
<article class="abs feature-card" style="left:424px">
  <h3><svg width="30" height="22" viewBox="0 0 30 22"><ellipse cx="11" cy="9" rx="10" ry="7" fill="#222"/><ellipse cx="21" cy="13" rx="8" ry="6" fill="#222"/><path d="M5 14l-2 6 6-4" fill="#222"/></svg>News &amp; Chatter</h3>
  <p>We like challenges and do complete these challenge with expertise we like solving questions that arises</p>
</article>
<article class="abs feature-card" style="left:625px">
  <h3><svg width="24" height="26" viewBox="0 0 24 26"><circle cx="12" cy="15" r="10" stroke="#222" stroke-width="2" fill="none"/><path d="M12 15V9M9 2h6" stroke="#222" stroke-width="2"/></svg>Demo</h3>
  <p>We like challenges and do complete these challenge with expertise we like solving questions that arises</p>
</article>

<footer class="abs footer">
  <div class="footer-col" style="left:44px">
    <svg width="44" height="22" viewBox="0 0 44 22"><path d="M2 18l12-14 4 3-12 14z" fill="#ddd"/><path d="M22 6l18 2-4 12-16-6z" stroke="#ddd" stroke-width="2" fill="none"/></svg>
    <div class="rule"></div>
    <ul style="margin-left:12px;font-size:11px;letter-spacing:.4px"><li>Search Marketing</li><li>Organic/Nature (SEO)</li><li>Social Media</li><li>Web Analysis</li></ul>
  </div>
  <div class="footer-col" style="left:250px">
    <svg width="42" height="24" viewBox="0 0 42 24"><rect x="1" y="6" width="24" height="16" fill="#ddd"/><path d="M1 6l12 9 12-9" stroke="#2d2d2d" stroke-width="1.5" fill="none"/><rect x="27" y="1" width="13" height="22" rx="2" stroke="#ddd" stroke-width="2" fill="none"/></svg>
    <div class="rule"></div>
    <ul><li>Contact Us</li><li>Customer Support</li><li>Request a Call back</li><li>FAQ's</li></ul>
  </div>
  <div class="footer-col" style="left:455px">
    <svg width="46" height="22" viewBox="0 0 46 22"><path d="M0 12h6l3-8 4 16 4-12 2 4h4" stroke="#ddd" stroke-width="2" fill="none"/><rect x="26" y="6" width="18" height="14" fill="#ddd"/><rect x="30" y="11" width="5" height="9" fill="#2d2d2d"/></svg>
    <div class="rule"></div>
    <ul><li>Sitemap</li><li>Terms &amp; Conditons</li><li>Privacy Settings</li></ul>
  </div>
  <div class="footer-col newsletter" style="left:634px">
    <svg width="36" height="24" viewBox="0 0 36 24"><circle cx="11" cy="11" r="10" fill="#ddd"/><path d="M11 5v7h5" stroke="#2d2d2d" stroke-width="2" fill="none"/><circle cx="27" cy="8" r="5" fill="#ddd"/><path d="M18 24c0-7 4-10 9-10s9 3 9 10z" fill="#ddd"/></svg>
    <p>Sign up for monthly Newsletters</p>
    <input type="email" placeholder="your email add">
  </div>
</footer>
<div class="abs bottom-bar">copyright © 2012 company name All right reserved</div>
</body>
</html>
```